Design a website for our small self storage business

We're looking for a freelance web designer who can produce a good-looking design for our small business website (no coding necessary). We will provide a list of pages to design, along with content outlines.

Key skills:
- Graphic design
- Responsive web design
- Proficiency with a modern web design tool such as Figma, Adobe Xd, or InVision

Please send relevant previous work (preferably in an inspectable format such as Figma or Invision).

```html
<!DOCTYPE html>
<html lang="en">
<head>
<meta charset="utf-8">
<title>Harbor Lane Storage</title>
<link href="https://fonts.googleapis.com/css2?family=Poppins:wght@500;600;700&family=Raleway:wght@400;500;600&display=swap" rel="stylesheet">
<style>
:root{
  --navy:#0b4588;
  --navy-dark:#0a3a74;
  --red:#e31b23;
  --ink:#2a2a2a;
  --body:#3b3b3b;
  --muted:#7c7c7c;
  --white:#ffffff;
  --panel:#f7f7f7;
  --black:#000000;
}
*{margin:0;padding:0;box-sizing:border-box}
html,body{width:1200px;height:2986px;overflow:hidden}
body{position:relative;background:var(--white);font-family:"Raleway",sans-serif;color:var(--body)}
.abs{position:absolute}

/* header */
.site-header{position:absolute;left:0;top:0;width:1200px;height:154px;background:var(--white)}
.brand{left:120px;top:36px;display:flex;align-items:center;gap:12px}
.brand-mark{width:30px;height:30px;background:var(--red)}
.brand-name{font-family:"Poppins",sans-serif;font-weight:700;color:var(--navy);font-size:26px;line-height:30px;letter-spacing:1px}
.contact-bar{top:24px;left:466px;display:flex;align-items:center;font-size:15px;color:var(--ink)}
.contact-item{display:flex;align-items:center;gap:12px}
.ring{width:42px;height:42px;border:2px solid var(--navy);border-radius:50%;display:flex;align-items:center;justify-content:center}
.divider{width:1px;height:22px;background:#ddd;margin:0 20px}
.social-top{top:36px;left:1004px;display:flex;gap:14px}
.social-top span{width:16px;height:16px;border-radius:50%;background:var(--navy)}
.main-nav{top:103px;left:383px;display:flex;gap:32px;font-size:16px;color:var(--ink)}
.main-nav .active{color:var(--navy)}
.search{top:102px;left:1065px}

/* hero */
.hero{left:0;top:154px;width:1200px;height:700px;background:linear-gradient(180deg,#4a3a30 0%,#8a6a4c 35%,#b8986e 60%,#6e5a4a 100%)}
.hero-cut{left:0;top:720px;width:1200px;height:134px}
.hero-copy{left:0;top:410px;width:1200px;text-align:center;color:var(--white);font-family:"Poppins",sans-serif}
.hero-copy .eyebrow{font-size:44px;font-weight:500;line-height:54px}
.hero-copy h1{font-size:62px;font-weight:700;line-height:74px}
.btn{display:inline-flex;align-items:center;justify-content:center;background:var(--navy);color:var(--white);font-family:"Poppins",sans-serif;font-weight:600;font-size:16px;border-radius:25px}
.hero-btn{left:530px;top:561px;width:140px;height:49px}
.arrow{top:478px}

/* features */
.photo-circle{border-radius:50%}
.feature h2{font-family:"Poppins",sans-serif;font-weight:500;font-size:32px;color:var(--ink);line-height:40px}
.feature p{font-size:16px;line-height:25.7px;text-align:justify;color:var(--body);margin-top:24px}
.feature .btn{width:143px;height:49px;margin-top:40px}

/* faq */
.faq-bg{left:0;top:1835px;width:1200px;height:800px;background:linear-gradient(160deg,#1d5ea8 0%,#0c4d96 50%,#17559e 100%)}
.faq-title{left:0;top:1912px;width:1200px;text-align:center;font-family:"Poppins",sans-serif;font-weight:600;font-size:33px;color:var(--white)}
.faq-list{left:111px;top:2005px;width:978px}
.faq-item{display:flex;background:var(--panel);margin-bottom:7px;min-height:61px}
.faq-num{width:70px;border-right:1px solid #ddd;font-family:"Poppins",sans-serif;font-size:18px;font-weight:500;color:var(--ink);text-align:center;padding-top:18px}
.faq-body{flex:1;padding:18px 34px 0;position:relative}
.faq-q{font-family:"Poppins",sans-serif;font-size:18px;color:#666}
.faq-toggle{position:absolute;right:26px;top:16px;font-size:20px;color:#777}
.faq-item.open .faq-num,.faq-item.open .faq-q{color:var(--red)}
.faq-a{font-size:16px;line-height:25.7px;color:#888;margin-top:26px;padding-bottom:26px}

/* footer */
.footer-cut{left:0;top:2470px;width:1200px;height:160px}
.footer{left:0;top:2620px;width:1200px;height:366px;background:var(--black);color:var(--white)}
.footer h3{position:absolute;top:76px;font-family:"Raleway",sans-serif;font-weight:600;font-size:22px}
.newsletter{left:110px;top:135px;width:284px;height:50px;border:1px solid #ccc;border-radius:25px;font-size:15px;padding:0 0 0 21px;display:flex;align-items:center;justify-content:space-between}
.newsletter .submit{width:86px;height:40px;border-radius:20px;background:var(--white);color:#555;font-size:15px;font-weight:500;display:flex;align-items:center;justify-content:center;margin-right:4px}
.links{left:475px;top:138px;font-size:16px;line-height:26px}
.contact-list{left:671px;top:138px;font-size:16px;line-height:26px}
.contact-list li{list-style:none;display:flex;gap:12px;margin-bottom:10px}
.contact-list svg{flex:none;margin-top:5px}
.social-foot{left:911px;top:140px;display:flex;gap:18px}
.social-foot span{width:20px;height:20px;border-radius:50%;background:var(--white)}
.copyright{left:0;top:2940px;width:1200px;text-align:center;font-size:16px;color:var(--white)}
</style>
</head>
<body>

<header class="site-header">
  <div class="abs brand">
    <span class="brand-mark"></span>
    <div class="brand-name">HARBOR LANE<br>STORAGE</div>
  </div>
  <div class="abs contact-bar">
    <div class="contact-item">
      <span class="ring"><svg width="16" height="16" viewBox="0 0 24 24"><path fill="#e31b23" d="M6.6 10.8a15 15 0 0 0 6.6 6.6l2.2-2.2a1 1 0 0 1 1-.25 11.4 11.4 0 0 0 3.6.57 1 1 0 0 1 1 1V20a1 1 0 0 1-1 1A17 17 0 0 1 3 4a1 1 0 0 1 1-1h3.5a1 1 0 0 1 1 1c0 1.250.2 2.450.57 3.57a1 1 0 0 1-.25 1z"/></svg></span>
      +1 (555) 010 2040
    </div>
    <span class="divider"></span>
    <div class="contact-item">
      <span class="ring"><svg width="16" height="14" viewBox="0 0 16 12"><rect width="16" height="12" rx="1" fill="#e31b23"/><path d="M1 1l7 5 7-5" stroke="#fff" stroke-width="1.5" fill="none"/></svg></span>
      hello@harborlanestorage.com
    </div>
  </div>
  <div class="abs social-top"><span></span><span></span><span></span></div>
  <nav class="abs main-nav">
    <span class="active">HOME</span><span>UNIT SIZES</span><span>SPECIALS</span><span>TESTIMONIALS</span><span>PAY ONLINE</span><span>CONTACT US</span>
  </nav>
  <svg class="abs search" width="22" height="22" viewBox="0 0 22 22"><circle cx="9" cy="9" r="7" stroke="#e31b23" stroke-width="3" fill="none"/><path d="M14 14l6 6" stroke="#e31b23" stroke-width="3" stroke-linecap="round"/></svg>
</header>

<section>
  <div class="abs hero" role="img" aria-label="Storage unit with open roller door, shelves stacked with cardboard boxes"></div>
  <svg class="abs hero-cut" width="1200" height="134" viewBox="0 0 1200 134">
    <polygon points="0,132 473,16 1200,132 1200,134 0,134" fill="#fff"/>
    <polyline points="0,130 473,16" stroke="#e31b23" stroke-width="9" fill="none"/>
    <polyline points="473,16 1200,130" stroke="#0b4588" stroke-width="9" fill="none"/>
  </svg>
  <svg class="abs arrow" style="left:62px" width="20" height="36" viewBox="0 0 20 36"><path d="M17 3L4 18l13 15" stroke="#e31b23" stroke-width="4" fill="none"/></svg>
  <svg class="abs arrow" style="left:1120px" width="20" height="36" viewBox="0 0 20 36"><path d="M3 3l13 15L3 33" stroke="#fff" stroke-width="4" fill="none"/></svg>
  <div class="abs hero-copy">
    <div class="eyebrow">Welcome To</div>
    <h1>Harbor Lane Storage</h1>
  </div>
  <a class="abs btn hero-btn">Our Units</a>
</section>

<section class="feature">
  <div class="abs photo-circle" style="left:114px;top:912px;width:368px;height:368px;border-right:7px solid var(--red);border-bottom:7px solid var(--red);background:radial-gradient(circle,#c9a57a 0%,#9ac94a 60%,#7ab832 100%)" role="img" aria-label="Cardboard boxes on a trolley in a green storage corridor"></div>
  <div class="abs" style="left:602px;top:920px;width:486px">
    <h2>Drive-up spaces</h2>
    <p>Lorem ipsum dolor sit amet, consectetur adipiscing elit, sed do eiusmod tempor incididunt ut labore et dolore magna aliqua. Ut enim ad minim veniam, quis nostrud exercitation ullamco laboris nisi ut aliquip ex ea commodo consequat. Duis aute irure dolor in reprehenderit in voluptate velit esse cillum dolore eu fugiat nulla pariatur. Excepteur sint occaecat cupidatat non proident, sunt in culpa qui officia deserunt mollit anim id est laborum.</p>
    <a class="btn">Learn More</a>
  </div>
</section>

<section class="feature">
  <div class="abs" style="left:114px;top:1392px;width:485px">
    <h2>Just show up with your stuff</h2>
    <p>Lorem ipsum dolor sit amet, consectetur adipiscing elit, sed do eiusmod tempor incididunt ut labore et dolore magna aliqua. Ut enim ad minim veniam, quis nostrud exercitation ullamco laboris nisi ut aliquip ex ea commodo consequat. Duis aute irure dolor in reprehenderit in voluptate velit esse cillum dolore eu fugiat nulla pariatur. Excepteur sint occaecat cupidatat non proident, sunt in culpa qui officia deserunt mollit anim id est laborum.</p>
    <a class="btn">Learn More</a>
  </div>
  <div class="abs photo-circle" style="left:719px;top:1383px;width:368px;height:368px;border-left:7px solid var(--navy);border-bottom:7px solid var(--navy);background:linear-gradient(120deg,#e8eaec 0%,#9aa4ae 50%,#2f4f78 100%)" role="img" aria-label="Indoor storage corridor with blue roller doors"></div>
</section>

<section>
  <div class="abs faq-bg" role="img" aria-label="Blue-toned view of a storage facility"></div>
  <svg class="abs footer-cut" width="1200" height="160" viewBox="0 0 1200 160">
    <polygon points="0,17 473,133 1200,23 1200,160 0,160" fill="#000"/>
    <polyline points="0,17 473,133 1200,23" stroke="#e31b23" stroke-width="9" fill="none"/>
  </svg>
  <h2 class="abs faq-title">Frequently Asked Questions</h2>
  <div class="abs faq-list">
    <div class="faq-item"><div class="faq-num">1</div><div class="faq-body"><div class="faq-q">Sed ut perspiciatis unde omnis iste natus error sit</div><span class="faq-toggle">+</span></div></div>
    <div class="faq-item open"><div class="faq-num">2</div><div class="faq-body"><div class="faq-q">what should I bring to rent a space?</div><span class="faq-toggle">–</span><div class="faq-a">Lorem ipsum dolor sit amet, consectetur adipiscing elit, sed do eiusmod tempor incididunt ut labore et aliqua. Ut enim ad minim veniam, quis nostrud exercitation ullamco laboris nisi ut aliquip.</div></div></div>
    <div class="faq-item"><div class="faq-num">3</div><div class="faq-body"><div class="faq-q">Lorem ipsum dolor sit amet, consectetur</div><span class="faq-toggle">+</span></div></div>
    <div class="faq-item"><div class="faq-num">4</div><div class="faq-body"><div class="faq-q">Lorem ipsum dolor sit amet, consectetur adipiscing elit,</div><span class="faq-toggle">+</span></div></div>
    <div class="faq-item"><div class="faq-num">5</div><div class="faq-body"><div class="faq-q">Lorem ipsum dolor sit amet, consectetur adipiscing elit, sed do eiusmod</div><span class="faq-toggle">+</span></div></div>
  </div>
</section>

<footer class="abs footer">
  <h3 style="left:112px">NEWSLETTER SIGN UP</h3>
  <h3 style="left:475px">QUICK LINKS</h3>
  <h3 style="left:671px">CONTACT US</h3>
  <h3 style="left:911px">SOCIAL MEDIA</h3>
  <div class="abs newsletter"><span>Your Email</span><span class="submit">SUBMIT</span></div>
  <div class="abs links">Home<br>Unit Sizes<br>Specials<br>Testimonials<br>Pay Online<br>Contact Us</div>
  <ul class="abs contact-list">
    <li><svg width="16" height="16" viewBox="0 0 24 24"><path fill="#fff" d="M6.6 10.8a15 15 0 0 0 6.6 6.6l2.2-2.2a1 1 0 0 1 1-.25 11.4 11.4 0 0 0 3.6.57 1 1 0 0 1 1 1V20a1 1 0 0 1-1 1A17 17 0 0 1 3 4a1 1 0 0 1 1-1h3.5a1 1 0 0 1 1 1c0 1.250.2 2.450.57 3.57a1 1 0 0 1-.25 1z"/></svg><span>+1 (555) 010 2040</span></li>
    <li><svg width="16" height="12" viewBox="0 0 16 12"><rect width="16" height="12" rx="1" fill="#fff"/><path d="M1 1l7 5 7-5" stroke="#000" stroke-width="1.5" fill="none"/></svg><span>2180 Harbor Lane<br>Elm Valley, CA 90000</span></li>
    <li><svg width="16" height="16" viewBox="0 0 16 16"><circle cx="8" cy="8" r="6.5" stroke="#fff" stroke-width="2" fill="none"/><path d="M8 4v4h3" stroke="#fff" stroke-width="2" fill="none"/></svg><span>9:30 AM - 5:30 PM<br>7 days a week</span></li>
  </ul>
  <div class="abs social-foot"><span></span><span></span><span></span><span></span><span></span></div>
</footer>
<div class="abs copyright">© 2022 Harbor Lane Storage</div>

</body>
</html>
```